Luxury Toilet Rental Business. Tallowby Hire.

Tallowby Hire (the logo is in the uploaded files)
We RENT and SELL Luxury Trailer toilets.
- Show location, number, pricing, pictures.
- We have two stall trailers for rent AND 3 stall trailers
- We sell them too
- We want our phone number shown
- We are a local company
- Slogan: Brighten your gathering with Tallowby Hire. The Velvet Privy
- We want a pricing portion
- We want the sizes shown
- We want the different rates/ prices shown
- We do 1 day rentals
- We do 1 week rentals
- We want the service area. We serve Los Angeles County, Orange County, Riverside County, San Bernardino County, and Palm Desert.
- Our location is in Santa Ana California

Target Market(s)

Event planners, wedding planners, venue planners, concerts, events, gatherings.

Industry/Entity Type

Luxury Toilet Rentals

Number of Pages Required

1 page

Font styles to use
Serif
Sans Serif

Colors
EE7325
F08F49
F5BC92
FAE3D3
FDF4ED

Requirements
Must have
• Location, pricing, pictures, available areas. Our slogan.
Nice to have
• I like the idea of having tabs that show price, a tab that shows our contact information, pictures, event ideas, and where we service (the areas we'll go to)

```html
<!DOCTYPE html>
<html lang="en">
<head>
<meta charset="utf-8">
<title>Tallowby Hire – Luxury Restroom Trailers</title>
<link rel="stylesheet" href="https://fonts.googleapis.com/css2?family=Audiowide&family=Lato:wght@400;700&display=swap">
<style>
:root{
  --orange:#ee7325;
  --orange-2:#f08f49;
  --orange-3:#f5bc92;
  --dark:#555555;
  --darker:#3f3f3f;
  --ink:#333333;
  --grey-bg:#f3f3f3;
  --btn-grey:#a6a6a6;
  --white:#ffffff;
}
*{box-sizing:border-box;margin:0;padding:0}
html,body{width:1200px;height:3715px;overflow:hidden}
body{font-family:"Lato",sans-serif;color:var(--ink);background:var(--white);position:relative}
.hl{color:var(--orange)}

/* top bar */
.topbar{height:58px;display:flex}
.topbar .left{width:600px;background:var(--dark);color:#fff;font-family:"Audiowide",sans-serif;font-size:13px;display:flex;align-items:center;padding-left:110px;gap:8px}
.topbar .right{flex:1;background:var(--orange);color:#fff;font-family:"Audiowide",sans-serif;font-size:15px;display:flex;align-items:center;justify-content:flex-end;padding-right:110px;gap:10px}

/* nav */
.nav{height:102px;position:relative;background:#fff;font-family:"Audiowide",sans-serif;font-size:14px;color:var(--dark)}
.nav a{color:inherit;text-decoration:none;position:absolute;top:44px;white-space:nowrap}
.brand-tab{position:absolute;left:441px;top:0;width:319px;height:117px;background:#fff;z-index:3;display:flex;align-items:center;justify-content:center;gap:10px}
.brand-tab .sq{width:16px;height:16px;background:var(--orange);flex:none}
.brand-tab .name{font-family:"Audiowide",sans-serif;font-size:25px;color:var(--dark);letter-spacing:1px;white-space:nowrap}
.nav .contact-btn{top:30px;left:947px;width:141px;height:42px;border:2px solid var(--dark);display:flex;align-items:center;justify-content:center}

/* hero */
.hero{height:592px;position:relative;background:linear-gradient(120deg,#6c6c6c 0%,#8a8a8a 35%,#5c5c5c 70%,#767676 100%)}
.hero-frame{position:absolute;left:314px;top:105px;width:590px;height:358px;border:8px solid #fff;border-bottom:none;text-align:center;color:#fff;font-family:"Audiowide",sans-serif}
.hero-frame .seg{position:absolute;bottom:0;height:8px;background:#fff}
.hero-frame .kicker{font-size:15px;margin-top:48px;letter-spacing:.5px}
.hero-frame h1{font-weight:400;font-size:29px;line-height:56px;margin-top:22px;letter-spacing:1px}
.hero-btn{position:absolute;left:516px;top:433px;width:186px;height:59px;background:#fff;color:var(--orange);font-family:"Audiowide",sans-serif;font-size:16px;display:flex;align-items:center;justify-content:center}

/* section title */
.sec-title{position:absolute;border:4px solid var(--dark);display:flex;align-items:center;justify-content:center;font-family:"Audiowide",sans-serif;font-size:32px;color:var(--dark);background:#fff;font-weight:400;white-space:nowrap}

/* services */
.services{height:651px;position:relative}
.area-card{position:absolute;top:174px;width:219px;height:297px;border:1px solid #cfcfcf;padding:6px}
.area-card .pic{height:236px}
.area-card p{text-align:center;font-family:"Audiowide",sans-serif;font-size:14px;color:var(--dark);margin-top:22px;white-space:nowrap}
.view-more{position:absolute;left:508px;top:522px;width:184px;height:60px;border:2px solid var(--orange);display:flex;align-items:center;justify-content:center;font-family:"Audiowide",sans-serif;font-size:17px;color:var(--dark);gap:6px}

/* rent/sell */
.units{height:596px;background:var(--grey-bg);position:relative}
.tab{position:absolute;top:75px;width:134px;height:60px;color:#fff;font-family:"Audiowide",sans-serif;font-size:16px;display:flex;align-items:center;justify-content:center}
.tab.rent{left:441px;background:var(--orange)}
.tab.sell{left:622px;background:var(--btn-grey)}
.unit{position:absolute;top:192px;width:371px;height:323px;background:#fff;box-shadow:0 2px 6px rgba(0,0,0,.12);text-align:center}
.unit .pic{height:239px}
.unit h3{font-weight:400;font-size:18px;color:#222;margin-top:16px}
.unit .size{font-size:14px;color:#666;margin-top:12px}

/* band */
.band{height:372px;position:relative;background:linear-gradient(120deg,#e2651d 0%,#ee7325 50%,#e8691f 100%);text-align:center;color:#fff}
.band h2{font-family:"Audiowide",sans-serif;font-weight:400;font-size:37px;line-height:52px;padding-top:50px}
.band .sub{font-family:"Audiowide",sans-serif;font-size:18px;margin-top:26px}
.band .btn{position:absolute;top:247px;height:57px;display:flex;align-items:center;justify-content:center;font-family:"Audiowide",sans-serif;font-size:16px}
.band .btn.day{left:275px;width:277px;background:#fff;color:var(--orange)}
.band .btn.week{left:636px;width:289px;background:#777;color:#fff;border:3px solid #9a9a9a}

/* pricing */
.pricing{height:940px;position:relative}
.plan{position:absolute;background:#fff;box-shadow:0 4px 10px rgba(0,0,0,.1)}
.plan .head{color:#fff;text-align:center;font-family:"Lato",sans-serif;font-weight:700}
.plan.side{top:300px;width:267px;height:453px}
.plan.side .head{height:117px;background:linear-gradient(#3a3a3a,#666);font-size:17px;padding-top:30px}
.plan.side .price{position:absolute;top:70px;left:50%;margin-left:-47px;width:94px;height:94px;border-radius:50%;background:#fff;border:6px solid var(--dark);display:flex;align-items:center;justify-content:center;font-size:28px;font-weight:700;color:var(--dark)}
.plan.side ul{margin-top:75px;padding:0 20px 0 26px}
.plan.side li{font-size:13px;line-height:19px;color:#555;margin-bottom:13px;display:flex;gap:14px}
.plan.vip{left:421px;top:193px;width:349px;height:667px;z-index:2}
.plan.vip .head{height:152px;background:linear-gradient(var(--orange),var(--orange-2));font-size:25px;padding-top:32px;font-weight:400}
.plan.vip .price{position:absolute;top:91px;left:50%;margin-left:-61px;width:122px;height:122px;border-radius:50%;background:#fff;border:7px solid var(--orange);display:flex;align-items:center;justify-content:center;font-size:33px;color:var(--orange)}
.plan.vip ul{margin-top:88px;padding:0 20px 0 16px}
.plan.vip li{font-size:16px;line-height:22px;color:#555;margin-bottom:19px;display:flex;gap:18px}
.plan ul{list-style:none}
.plan li svg{flex:none;margin-top:3px}

/* footer */
.footer{height:404px;background:var(--dark);position:relative;color:#fff}
.f-brand{position:absolute;left:114px;top:76px;width:270px;display:flex;align-items:center;gap:10px;font-family:"Audiowide",sans-serif;font-size:23px;white-space:nowrap;letter-spacing:.5px}
.f-brand .sq{width:16px;height:16px;background:var(--orange);flex:none}
.socials{position:absolute;left:112px;top:157px;display:flex;gap:26px}
.socials span{width:32px;height:32px;border-radius:50%;background:#fff}
.f-col{position:absolute;top:77px}
.f-col h4{font-family:"Audiowide",sans-serif;font-weight:400;font-size:18px;margin-bottom:18px;white-space:nowrap}
.f-col li{list-style:none;font-size:15px;margin-bottom:14px;display:flex;align-items:center;gap:9px;white-space:nowrap}
.f-contact li{align-items:flex-start;gap:14px;line-height:27px;margin-bottom:16px}
.f-contact .ic{width:32px;height:32px;border-radius:50%;background:#fff;display:flex;align-items:center;justify-content:center;flex:none}
.f-rule{position:absolute;left:111px;right:111px;top:323px;border-top:1px solid #8a8a8a}
.copy{position:absolute;top:358px;width:100%;text-align:center;font-size:15px}
</style>
</head>
<body>

<header class="topbar">
  <div class="left">
    <svg width="13" height="13" viewBox="0 0 24 24" fill="#fff"><path d="M6.6 10.8a15 15 0 0 0 6.6 6.6l2.2-2.2a1 1 0 0 1 1-.25 11.4 11.4 0 0 0 3.6.57 1 1 0 0 1 1 1V20a1 1 0 0 1-1 1A17 17 0 0 1 3 4a1 1 0 0 1 1-1h3.5a1 1 0 0 1 1 1c0 1.25.2 2.45.57 3.6a1 1 0 0 1-.25 1z"/></svg>
    +1 555 014 2290
  </div>
  <div class="right">
    <svg width="14" height="18" viewBox="0 0 24 30" fill="#fff"><path d="M12 0a10 10 0 0 0-10 10c0 7.5 10 20 10 20s10-12.5 10-20A10 10 0 0 0 12 0zm0 14a4 4 0 1 1 0-8 4 4 0 0 1 0 8z"/></svg>
    Santa Ana California
  </div>
</header>

<nav class="nav">
  <a style="left:110px">HOME</a>
  <a style="left:210px">ABOUT</a>
  <a style="left:320px">SERVICES</a>
  <div class="brand-tab"><span class="sq"></span><span class="name">TALLOWBY HIRE</span></div>
  <a style="left:829px">PRICING</a>
  <a class="contact-btn">CONTACT&nbsp;<span class="hl">US</span></a>
</nav>

<section class="hero" role="img" aria-label="Interior of a luxury restroom trailer with vanity sink and toilet">
  <div class="hero-frame">
    <p class="kicker">WELCOME TO TALLOWBY HIRE</p>
    <h1>BRIGHTEN YOUR GATHERING<br>WITH <span class="hl">TALLOWBY HIRE.</span><br>THE VELVET PRIVY</h1>
    <span class="seg" style="left:-8px;width:202px"></span>
    <span class="seg" style="right:-8px;width:202px"></span>
  </div>
  <a class="hero-btn">GET STARTED</a>
</section>

<section class="services">
  <h2 class="sec-title" style="left:358px;top:59px;width:483px;height:72px">OUR&nbsp;<span class="hl">SERVICES AREA</span></h2>
  <div class="area-card" style="left:111px"><div class="pic" role="img" aria-label="Los Angeles skyline aerial view" style="background:linear-gradient(#9cc3e6 0%,#b7cbd8 30%,#4f6a44 55%,#35502e 100%)"></div><p>LOS ANGELES</p></div>
  <div class="area-card" style="left:364px"><div class="pic" role="img" aria-label="Orange County harbor aerial view" style="background:linear-gradient(#5a9be0 0%,#8cb6dc 25%,#8a9a84 55%,#2d7ba8 100%)"></div><p>ORANGE COUNTRY</p></div>
  <div class="area-card" style="left:616px"><div class="pic" role="img" aria-label="Coastal cliffs above the sea" style="background:linear-gradient(#5d8fc4 0%,#c9d8e6 30%,#3f6b3a 55%,#2e7a8c 100%)"></div><p>RIVERSIDE COUNTRY</p></div>
  <div class="area-card" style="left:869px"><div class="pic" role="img" aria-label="Palm tree in desert dunes at sunset" style="background:linear-gradient(#6f7f8f 0%,#d69a5a 45%,#b8702f 75%,#8a5526 100%)"></div><p>PALM DESERT</p></div>
  <a class="view-more">VIEW <span class="hl">MORE</span></a>
</section>

<section class="units">
  <a class="tab rent">RENT</a>
  <a class="tab sell">SELL</a>
  <article class="unit" style="left:26px"><div class="pic" role="img" aria-label="Vanity sink with white cabinet" style="background:linear-gradient(135deg,#e8e8e8,#c9c9c9 60%,#a89a86)"></div><h3>Temporibus autem quibusdam</h3><p class="size">Size: 10 ft</p></article>
  <article class="unit" style="left:415px"><div class="pic" role="img" aria-label="Grey restroom trailer with three doors and blue steps" style="background:linear-gradient(#b8bcc0 0%,#9a9ea2 40%,#6d7276 60%,#8c8c88 100%)"></div><h3>Itaque earum rerum</h3><p class="size">Size: 20 ft</p></article>
  <article class="unit" style="left:803px"><div class="pic" role="img" aria-label="Restroom interior with toilet and sink" style="background:linear-gradient(#d4d6d8,#eeeeee 50%,#c9bba8)"></div><h3>Reiciendis voluptatibus maiores</h3><p class="size">Size: 15 ft</p></article>
</section>

<section class="band">
  <h2>We have two stall trailers for rent<br>AND 3 stall trailers</h2>
  <p class="sub">WE ARE A LOCAL COMPANY</p>
  <a class="btn day">WE DO 1 DAY RENTALS</a>
  <a class="btn week">WE DO 1 WEEK RENTALS</a>
</section>

<section class="pricing">
  <h2 class="sec-title" style="left:434px;top:69px;width:330px;height:72px">OUR&nbsp;<span class="hl">PRICING</span></h2>

  <div class="plan side" style="left:160px">
    <div class="head">THE ULTIMATE PACKAGE</div>
    <div class="price">$150</div>
    <ul>
      <li><svg width="12" height="10" viewBox="0 0 12 10"><path d="M1 5l3.5 3.5L11 1.5" stroke="#555" stroke-width="2.4" fill="none"/></svg>Itaque earum rerum</li>
      <li><svg width="12" height="10" viewBox="0 0 12 10"><path d="M1 5l3.5 3.5L11 1.5" stroke="#555" stroke-width="2.4" fill="none"/></svg>Btenetur a sapiente delectus, ut aut reiciendis</li>
      <li><svg width="12" height="10" viewBox="0 0 12 10"><path d="M1 5l3.5 3.5L11 1.5" stroke="#555" stroke-width="2.4" fill="none"/></svg>Voluptatibus maiores</li>
      <li><svg width="12" height="10" viewBox="0 0 12 10"><path d="M1 5l3.5 3.5L11 1.5" stroke="#555" stroke-width="2.4" fill="none"/></svg>Aalias consequatur aut perf</li>
      <li><svg width="12" height="10" viewBox="0 0 12 10"><path d="M1 5l3.5 3.5L11 1.5" stroke="#555" stroke-width="2.4" fill="none"/></svg>Doloribus asperiores est et expedita repellat</li>
      <li><svg width="12" height="10" viewBox="0 0 12 10"><path d="M1 5l3.5 3.5L11 1.5" stroke="#555" stroke-width="2.4" fill="none"/></svg>Nam libero tempore, cum</li>
      <li><svg width="12" height="10" viewBox="0 0 12 10"><path d="M1 5l3.5 3.5L11 1.5" stroke="#555" stroke-width="2.4" fill="none"/></svg>Soluta nobis est eligendi</li>
    </ul>
  </div>

  <div class="plan vip">
    <div class="head">THE VIP PACKAGE</div>
    <div class="price">$200</div>
    <ul>
      <li><svg width="15" height="12" viewBox="0 0 12 10"><path d="M1 5l3.5 3.5L11 1.5" stroke="#ee7325" stroke-width="2.4" fill="none"/></svg>At vero eos et accusamus et iusto</li>
      <li><svg width="15" height="12" viewBox="0 0 12 10"><path d="M1 5l3.5 3.5L11 1.5" stroke="#ee7325" stroke-width="2.4" fill="none"/></svg>Dignissimos ducimus qui blanditiis praesentium voluptatum</li>
      <li><svg width="15" height="12" viewBox="0 0 12 10"><path d="M1 5l3.5 3.5L11 1.5" stroke="#ee7325" stroke-width="2.4" fill="none"/></svg>Deleniti atque corrupti</li>
      <li><svg width="15" height="12" viewBox="0 0 12 10"><path d="M1 5l3.5 3.5L11 1.5" stroke="#ee7325" stroke-width="2.4" fill="none"/></svg>Facilis est et expedita distinctio</li>
      <li><svg width="15" height="12" viewBox="0 0 12 10"><path d="M1 5l3.5 3.5L11 1.5" stroke="#ee7325" stroke-width="2.4" fill="none"/></svg>Omnis voluptas assumenda est</li>
      <li><svg width="15" height="12" viewBox="0 0 12 10"><path d="M1 5l3.5 3.5L11 1.5" stroke="#ee7325" stroke-width="2.4" fill="none"/></svg>Itaque earum rerum hic tenetur</li>
      <li><svg width="15" height="12" viewBox="0 0 12 10"><path d="M1 5l3.5 3.5L11 1.5" stroke="#ee7325" stroke-width="2.4" fill="none"/></svg>Voluptatum deleniti atque corrupti</li>
      <li><svg width="15" height="12" viewBox="0 0 12 10"><path d="M1 5l3.5 3.5L11 1.5" stroke="#ee7325" stroke-width="2.4" fill="none"/></svg>Culpa qui officia deserunt mollitia</li>
      <li><svg width="15" height="12" viewBox="0 0 12 10"><path d="M1 5l3.5 3.5L11 1.5" stroke="#ee7325" stroke-width="2.4" fill="none"/></svg>Hcum soluta nobis est eligend</li>
      <li><svg width="15" height="12" viewBox="0 0 12 10"><path d="M1 5l3.5 3.5L11 1.5" stroke="#ee7325" stroke-width="2.4" fill="none"/></svg>Quo minus id quod maxime placeat</li>
    </ul>
  </div>

  <div class="plan side" style="left:770px">
    <div class="head">THE ULTIMATE PACKAGE 2</div>
    <div class="price">$160</div>
    <ul>
      <li><svg width="12" height="10" viewBox="0 0 12 10"><path d="M1 5l3.5 3.5L11 1.5" stroke="#555" stroke-width="2.4" fill="none"/></svg>Itaque earum rerum</li>
      <li><svg width="12" height="10" viewBox="0 0 12 10"><path d="M1 5l3.5 3.5L11 1.5" stroke="#555" stroke-width="2.4" fill="none"/></svg>Btenetur a sapiente delectus, ut aut reiciendis</li>
      <li><svg width="12" height="10" viewBox="0 0 12 10"><path d="M1 5l3.5 3.5L11 1.5" stroke="#555" stroke-width="2.4" fill="none"/></svg>Voluptatibus maiores</li>
      <li><svg width="12" height="10" viewBox="0 0 12 10"><path d="M1 5l3.5 3.5L11 1.5" stroke="#555" stroke-width="2.4" fill="none"/></svg>Aalias consequatur aut perf</li>
      <li><svg width="12" height="10" viewBox="0 0 12 10"><path d="M1 5l3.5 3.5L11 1.5" stroke="#555" stroke-width="2.4" fill="none"/></svg>Doloribus asperiores est et expedita repellat</li>
      <li><svg width="12" height="10" viewBox="0 0 12 10"><path d="M1 5l3.5 3.5L11 1.5" stroke="#555" stroke-width="2.4" fill="none"/></svg>Nam libero tempore, cum</li>
      <li><svg width="12" height="10" viewBox="0 0 12 10"><path d="M1 5l3.5 3.5L11 1.5" stroke="#555" stroke-width="2.4" fill="none"/></svg>Soluta nobis est eligendi</li>
    </ul>
  </div>
</section>

<footer class="footer">
  <div class="f-brand"><span class="sq"></span>TALLOWBY HIRE</div>
  <div class="socials"><span></span><span></span><span></span><span></span></div>

  <div class="f-col" style="left:456px">
    <h4>QUICK LINKS</h4>
    <ul>
      <li><svg width="10" height="12" viewBox="0 0 10 12"><path d="M2 1l6 5-6 5" stroke="#fff" stroke-width="2.4" fill="none"/></svg>Home</li>
      <li><svg width="10" height="12" viewBox="0 0 10 12"><path d="M2 1l6 5-6 5" stroke="#fff" stroke-width="2.4" fill="none"/></svg>About</li>
      <li><svg width="10" height="12" viewBox="0 0 10 12"><path d="M2 1l6 5-6 5" stroke="#fff" stroke-width="2.4" fill="none"/></svg>Service Area</li>
      <li><svg width="10" height="12" viewBox="0 0 10 12"><path d="M2 1l6 5-6 5" stroke="#fff" stroke-width="2.4" fill="none"/></svg>Rentals</li>
      <li><svg width="10" height="12" viewBox="0 0 10 12"><path d="M2 1l6 5-6 5" stroke="#fff" stroke-width="2.4" fill="none"/></svg>Contact Us</li>
    </ul>
  </div>

  <div class="f-col" style="left:662px">
    <h4>HELP LINKS</h4>
    <ul>
      <li><svg width="10" height="12" viewBox="0 0 10 12"><path d="M2 1l6 5-6 5" stroke="#fff" stroke-width="2.4" fill="none"/></svg>FAQ</li>
      <li><svg width="10" height="12" viewBox="0 0 10 12"><path d="M2 1l6 5-6 5" stroke="#fff" stroke-width="2.4" fill="none"/></svg>Terms of use</li>
      <li><svg width="10" height="12" viewBox="0 0 10 12"><path d="M2 1l6 5-6 5" stroke="#fff" stroke-width="2.4" fill="none"/></svg>Privacy Policy</li>
      <li><svg width="10" height="12" viewBox="0 0 10 12"><path d="M2 1l6 5-6 5" stroke="#fff" stroke-width="2.4" fill="none"/></svg>Support Links</li>
      <li><svg width="10" height="12" viewBox="0 0 10 12"><path d="M2 1l6 5-6 5" stroke="#fff" stroke-width="2.4" fill="none"/></svg>Conditions</li>
    </ul>
  </div>

  <div class="f-col f-contact" style="left:877px">
    <h4>CONTACT US</h4>
    <ul>
      <li><span class="ic"><svg width="13" height="17" viewBox="0 0 24 30" fill="#555"><path d="M12 0a10 10 0 0 0-10 10c0 7.5 10 20 10 20s10-12.5 10-20A10 10 0 0 0 12 0zm0 14a4 4 0 1 1 0-8 4 4 0 0 1 0 8z"/></svg></span><span>Tallowby Hire<br>Santa Ana California</span></li>
      <li><span class="ic"><svg width="15" height="15" viewBox="0 0 24 24" fill="#555"><path d="M6.6 10.8a15 15 0 0 0 6.6 6.6l2.2-2.2a1 1 0 0 1 1-.25 11.4 11.4 0 0 0 3.6.57 1 1 0 0 1 1 1V20a1 1 0 0 1-1 1A17 17 0 0 1 3 4a1 1 0 0 1 1-1h3.5a1 1 0 0 1 1 1c0 1.25.2 2.45.57 3.6a1 1 0 0 1-.25 1z"/></svg></span><span>+1 555 014 2290</span></li>
      <li><span class="ic"><svg width="16" height="12" viewBox="0 0 16 12"><rect x="1" y="1" width="14" height="10" fill="none" stroke="#555" stroke-width="1.8"/><path d="M1 1l7 6 7-6" fill="none" stroke="#555" stroke-width="1.8"/></svg></span><span>info@tallowbyhire.com</span></li>
    </ul>
  </div>

  <div class="f-rule"></div>
  <p class="copy">Copyrights@2024.Tallowby Hire.All Rights Reserved</p>
</footer>

</body>
</html>
```